BrivoTerna. Lantern of the Steady Harvest. Business card

Professional business card for BrivoTerna (Lantern of the Steady Harvest)
My rationale: Strategy-> Execution-> Results-> Value that lead to the BrivoTerna name: We put the Lantern of the Steady Harvest.
We deliver value to our customers helping them at defining a good strategy (cyan arrow). 90% of well formulated strategies fail due to poor execution so we also consider strategical execution very important (green arrow). Due to the execution we obtain the results (blue arrow). Finally, the results provide feedback to redefine strategy, and the new strategy has to be executed and new results obtained providing new feedback and on and on. It's like a wheel that finally, must create corporate value: value for shareholders, staholders, employees, providers...-

Target Market(s)

CEOs and steering comitees , invewrnent funds

Industry/Entity Type

Business Consultant

Contact Information for Business Card

Teodoro Vinsquel
CEO & Founder
teodoro.vinsquel@brivoterna-example.com
Mobile: +34 655.803.912
www.brivoterna-example.com

Colors

Designer to choose colors to be used in the design.

Requirements
Nice to have
• Nice to hace the words: Strategy, execution, results
• Nice to vave the claim: Lantern of the Steady Harvest
• The three colors should be shown:
• cyan for STRATEGY
• green for EXECUTION
• blue for RESULTS
Should not have
• Complete black background

```html
<!DOCTYPE html>
<html lang="en">
<head>
<meta charset="utf-8">
<title>BrivoTerna — Business Card</title>
<link rel="stylesheet" href="https://fonts.googleapis.com/css2?family=Open+Sans:ital,wght@0,400;0,600;0,700;1,400&family=Roboto:wght@700&display=swap">
<style>
  :root {
    --page-bg: #e8ecf0;
    --card-bg: #fbfbfa;
    --ink: #1a1a1a;
    --ink-soft: #3c3c3c;
    --band-blue: #34508f;
    --band-green: #8cbf4f;
    --band-cyan: #2fa0d8;
    --brand-navy: #1e3577;
    --label-white: #ffffff;
  }
  html, body {
    margin: 0;
    padding: 0;
    width: 1200px;
    height: 720px;
    overflow: hidden;
    background: var(--page-bg);
  }
  .canvas {
    position: relative;
    width: 1200px;
    height: 720px;
  }
  .card {
    position: absolute;
    top: 210px;
    width: 525px;
    height: 300px;
    background: var(--card-bg);
    box-shadow: 0 10px 24px rgba(20, 40, 70, 0.22);
    overflow: hidden;
  }
  .card--front { left: 45px; }
  .card--back { left: 630px; }

  .card__bands {
    position: absolute;
    inset: 0;
    width: 525px;
    height: 300px;
  }
  .band--blue { fill: var(--band-blue); }
  .band--green { fill: var(--band-green); }
  .band--cyan { fill: var(--band-cyan); }

  .holder {
    position: absolute;
    left: 47px;
    top: 55px;
  }
  .holder__name {
    margin: 0;
    font-family: "Roboto", sans-serif;
    font-weight: 700;
    font-size: 20px;
    color: var(--ink);
    letter-spacing: 0.1px;
  }
  .holder__role {
    margin: 3px 0 0;
    font-family: "Open Sans", sans-serif;
    font-size: 15.5px;
    letter-spacing: 1.2px;
    color: var(--ink-soft);
  }

  .contacts {
    position: absolute;
    left: 44px;
    top: 164px;
    margin: 0;
    padding: 0;
    list-style: none;
  }
  .contacts__item {
    display: flex;
    align-items: center;
    height: 34px;
    font-family: "Open Sans", sans-serif;
    font-size: 15px;
    letter-spacing: -0.2px;
    color: var(--ink-soft);
  }
  .contacts__icon {
    width: 16px;
    height: 16px;
    margin-right: 10px;
    fill: none;
    stroke: var(--ink-soft);
    stroke-width: 1.3;
  }

  .pillar {
    position: absolute;
    left: 0;
    font-family: "Open Sans", sans-serif;
    font-style: italic;
    font-size: 21px;
    color: var(--label-white);
    letter-spacing: 0.2px;
  }
  .pillar--results { top: 36px; left: 51px; }
  .pillar--execution { top: 141px; left: 48px; }
  .pillar--strategy { top: 240px; left: 48px; }

  .brand-name {
    position: absolute;
    left: 275px;
    top: 165px;
    width: 180px;
    text-align: center;
    font-family: "Open Sans", sans-serif;
    font-weight: 700;
    font-size: 34px;
    letter-spacing: -0.8px;
    color: var(--brand-navy);
  }
</style>
</head>
<body>
<main class="canvas">

  <section class="card card--front" aria-label="Business card front">
    <svg class="card__bands" viewBox="0 0 525 300" aria-hidden="true">
      <polygon class="band--blue" points="472,0 525,0 525,94 443,94"/>
      <polygon class="band--green" points="443,94 525,94 525,202 409,202"/>
      <polygon class="band--cyan" points="409,202 525,202 525,300 470,300"/>
    </svg>

    <div class="holder">
      <h1 class="holder__name">Teodoro Vinsquel</h1>
      <p class="holder__role">CEO &amp; Founder</p>
    </div>

    <ul class="contacts">
      <li class="contacts__item">
        <svg class="contacts__icon" viewBox="0 0 16 16" aria-hidden="true">
          <rect x="4" y="1.5" width="8" height="13" rx="1.2"/>
          <line x1="6.5" y1="12" x2="9.5" y2="12"/>
        </svg>
        +34 655.803.912
      </li>
      <li class="contacts__item">
        <svg class="contacts__icon" viewBox="0 0 16 16" aria-hidden="true">
          <rect x="1.5" y="3.5" width="13" height="9.5" rx="1"/>
          <polyline points="1.5,4 8,9 14.5,4"/>
        </svg>
        teodoro.vinsquel@brivoterna-example.com
      </li>
      <li class="contacts__item">
        <svg class="contacts__icon" viewBox="0 0 16 16" aria-hidden="true">
          <circle cx="8" cy="8" r="6.5"/>
          <ellipse cx="8" cy="8" rx="3" ry="6.5"/>
          <line x1="1.5" y1="8" x2="14.5" y2="8"/>
        </svg>
        www.brivoterna-example.com
      </li>
    </ul>
  </section>

  <section class="card card--back" aria-label="Business card back">
    <svg class="card__bands" viewBox="0 0 525 300" aria-hidden="true">
      <polygon class="band--blue" points="0,0 162,0 222,97 0,97"/>
      <polygon class="band--green" points="0,97 222,97 188,205 0,205"/>
      <polygon class="band--cyan" points="0,205 188,205 160,300 0,300"/>
    </svg>

    <span class="pillar pillar--results">RESULTS</span>
    <span class="pillar pillar--execution">EXECUTION</span>
    <span class="pillar pillar--strategy">STRATEGY</span>

    <div class="brand-name">BrivoTerna</div>
  </section>

</main>
</body>
</html>
```